Harborlight Amusement Collective (HAC)

We need a business card design for Harborlight Amusement Collective. Modern and sleek looking, with all critical information. Open to single or double sided designs, if double sided info needs to be all on one side. The main Logo is Harborlight Amusement collective and must be on the card. The other three logos are for the brands that fall under the group, they might be good on the back.

Industry/Entity Type

Business

```html
<!DOCTYPE html>
<html lang="en">
<head>
<meta charset="utf-8">
<title>Harborlight Amusement Collective – Business Card</title>
<link rel="stylesheet" href="https://fonts.googleapis.com/css2?family=Fira+Sans:wght@600&family=Montserrat:wght@400;600&display=swap">
<style>
  :root {
    --page-bg: #e9e7e4;
    --card-blue: #2d5a94;
    --card-blue-deep: #234a80;
    --card-frost: #e4e3e1;
    --card-frost-edge: #d3d2d0;
    --accent-green: #7f9a2e;
    --brand-blue: #264f8c;
    --text-light: #f2f4f7;
    --text-soft: #dfe6f0;
  }
  html, body {
    margin: 0;
    width: 1200px;
    height: 1054px;
    overflow: hidden;
    background: var(--page-bg);
  }
  .business-card {
    position: absolute;
    left: 100px;
    top: 226px;
    width: 1000px;
    height: 603px;
    box-shadow: 0 14px 36px rgba(0, 0, 0, 0.18);
  }
  .business-card svg { display: block; width: 100%; height: 100%; }
  .holder-name { font-family: "Fira Sans", sans-serif; font-weight: 600; font-size: 30px; fill: var(--text-light); }
  .holder-role { font-family: "Montserrat", sans-serif; font-weight: 400; font-size: 17px; fill: var(--text-soft); }
  .contact-line { font-family: "Montserrat", sans-serif; font-weight: 400; font-size: 17px; fill: var(--text-soft); }
  .contact-icon { fill: var(--text-soft); }
  .brand-name { font-family: "Montserrat", sans-serif; font-weight: 600; fill: var(--brand-blue); }
  .brand-mark { fill: var(--brand-blue); }
</style>
</head>
<body>
  <div class="business-card">
    <svg viewBox="0 0 787 475" xmlns="http://www.w3.org/2000/svg" aria-label="Harborlight Amusement Collective business card">
      <defs>
        <linearGradient id="frostFill" x1="0" y1="0" x2="1" y2="1">
          <stop offset="0" stop-color="var(--card-frost)"/>
          <stop offset="1" stop-color="var(--card-frost-edge)"/>
        </linearGradient>
        <linearGradient id="blueFill" x1="0" y1="0" x2="1" y2="1">
          <stop offset="0" stop-color="var(--card-blue)"/>
          <stop offset="1" stop-color="var(--card-blue-deep)"/>
        </linearGradient>
      </defs>

      <!-- card base -->
      <rect class="card-base" width="787" height="475" fill="url(#frostFill)"/>

      <!-- green accent arc -->
      <path class="accent-arc" d="M470,0 Q398,240 478,475 H462 Q410,240 481,0 Z" fill="var(--accent-green)"/>

      <!-- blue panel -->
      <path class="info-panel" d="M0,0 H481 Q400,240 462,475 H0 Z" fill="url(#blueFill)"/>

      <!-- holder -->
      <text class="holder-name" x="42" y="84">Marcus Reed Whitfield</text>
      <text class="holder-role" x="42" y="113">Managing Director</text>

      <!-- address -->
      <text class="contact-line" x="42" y="311">78 Beacon Quay Rd., Port</text>
      <text class="contact-line" x="42" y="337">Town, US 204518</text>

      <!-- phone -->
      <path class="contact-icon" d="M43,364 q8,-6 16,0 v3 h-4 v-2 q-4,-2 -8,0 v2 h-4 z M44,369 h14 l2,7 h-18 z"/>
      <text class="contact-line" x="81" y="375">555.204.7781</text>

      <!-- email -->
      <rect class="contact-icon" x="43" y="391" width="16" height="11" rx="1"/>
      <path d="M43,392 l8,6 l8,-6" fill="none" stroke="var(--card-blue)" stroke-width="1.4"/>
      <text class="contact-line" x="81" y="402">mreed@harborlightac.com</text>

      <!-- web -->
      <circle cx="51" cy="423" r="7.5" fill="none" stroke="var(--text-soft)" stroke-width="1.6"/>
      <ellipse cx="51" cy="423" rx="3" ry="7.5" fill="none" stroke="var(--text-soft)" stroke-width="1.2"/>
      <line x1="43.5" y1="423" x2="58.5" y2="423" stroke="var(--text-soft)" stroke-width="1.2"/>
      <text class="contact-line" x="81" y="429">www.harborlightac.com</text>

      <!-- brand -->
      <circle class="brand-mark" cx="562" cy="237" r="44"/>
      <g transform="translate(688 440) rotate(-90)">
        <text class="brand-name" x="0" y="0" font-size="23.5" textLength="395" lengthAdjust="spacingAndGlyphs">HARBORLIGHT AMUSEMENT</text>
        <text class="brand-name" x="0" y="36" font-size="19" letter-spacing="10" textLength="395" lengthAdjust="spacing">COLLECTIVE</text>
      </g>
    </svg>
  </div>
</body>
</html>
```